Marrowby Water Taxi and Transport Business Card

I need business cards for my new water taxi and freight transport business I have started here in Kodiak Alaska. Kodiak is a remote island in the middle of the gulf of Alaska. There are seven native villages around the island and Kodiak is the #2 fishing port in the United States. We also have the largest Coast Guard Base in the U.S. My company will be providing water taxi and freight transport logistics to the villages and many hunting and fishing lodges as well as remote properties around the island.

I would like a business card that isn't status quo, something that stands out, either in feel or appearance. I do like clean minimal designs but it needs to have the necessary contact info on it.

Target Market(s)

remote lodge / property owners, residents of the many villages around Kodiak and any one wanting to enjoy the great outdoors of Kodiak Alaska

Industry/Entity Type

Business

Contact Information for Business Card

I like clean simple designs that aren't cluttered but still provide the necessary information

Colors
0255a3
3277b5
33a4d5
9bcb3c
add136
fbed22
ffc214
f78f20
f37122

Requirements
Must have
• logo and contact info
• Captain Mason Elwick
• www.marrowbyferryline.com
• mason@marrowbyferryline.com

```html
<!DOCTYPE html>
<html lang="en">
<head>
<meta charset="utf-8">
<title>Marrowby Water Taxi and Transport – Business Card</title>
<link rel="stylesheet" href="https://fonts.googleapis.com/css2?family=Open+Sans:wght@400;600;700&display=swap">
<style>
  :root {
    --stage: #000000;
    --card-white: #ffffff;
    --brand-navy: #0255a3;
    --brand-blue: #3277b5;
    --brand-sky: #33a4d5;
    --text-dark: #1d1d1d;
    --sea-deep: #1f4f86;
    --sea-mid: #3f79b4;
    --sea-foam: #c9def0;
    --sky-pale: #eef3f7;
    --shore: #5d6f80;
  }
  * { margin: 0; padding: 0; box-sizing: border-box; }
  html, body {
    width: 1200px; height: 900px; overflow: hidden;
    background: var(--stage);
    font-family: "Open Sans", sans-serif;
  }
  .stage { position: relative; width: 1200px; height: 900px; }

  .card {
    position: absolute; top: 275px;
    width: 477px; height: 293px;
    overflow: hidden; background: var(--card-white);
  }
  .card--front { left: 116px; border-radius: 0 56px 0 56px; }
  .card--back  { left: 622px; border-radius: 56px 0 56px 0; }

  .sea-photo { position: absolute; left: 0; right: 0; bottom: 0; }
  .card--front .sea-photo {
    top: 150px;
    background:
      radial-gradient(ellipse 90px 70px at 38% 75%, var(--sea-foam), transparent 70%),
      linear-gradient(180deg, rgba(255,255,255,1) 0%, rgba(255,255,255,0.6) 22%, var(--sea-mid) 55%, var(--sea-deep) 100%);
  }
  .card--back .sea-photo {
    top: 0;
    background:
      radial-gradient(ellipse 110px 90px at 30% 78%, var(--sea-foam), transparent 70%),
      radial-gradient(ellipse 140px 40px at 80% 52%, #f4f0d8, transparent 70%),
      linear-gradient(180deg, #ffffff 0%, var(--sky-pale) 30%, #9fb3c5 44%, var(--sea-mid) 60%, var(--sea-deep) 100%);
  }

  .holder {
    position: absolute; left: 35px; top: 52px;
    font-size: 17px; font-weight: 600; color: var(--brand-navy);
  }
  .contact-list {
    position: absolute; left: 35px; top: 96px;
    list-style: none; font-size: 12.5px; color: var(--text-dark);
  }
  .contact-list li { display: flex; align-items: center; gap: 8px; height: 20px; }
  .contact-list svg { width: 11px; height: 11px; fill: var(--brand-navy); }

  .wordmark {
    position: absolute; text-align: center;
    color: var(--brand-navy); font-weight: 600; line-height: 1.1;
  }
  .wordmark .name { display: block; }
  .card--front .wordmark { left: 255px; top: 118px; width: 195px; }
  .card--front .wordmark .name { font-size: 36px; }
  .card--front .wordmark .tagline { font-size: 14px; }
  .card--back .wordmark { left: 90px; top: 40px; width: 300px; }
  .card--back .wordmark .name { font-size: 52px; }
  .card--back .wordmark .tagline { font-size: 20px; }
</style>
</head>
<body>
<main class="stage">
  <section class="card card--front" aria-label="Business card front">
    <div class="sea-photo" role="img" aria-label="Photo of a boat wake on open water with distant island shoreline"></div>
    <p class="holder">Captain Mason Elwick</p>
    <ul class="contact-list">
      <li>
        <svg viewBox="0 0 12 12" aria-hidden="true"><path d="M0 2h12v8H0z M0 2l6 4 6-4" stroke="#fff" stroke-width="0.8"/></svg>
        mason@marrowbyferryline.com
      </li>
      <li>
        <svg viewBox="0 0 12 12" aria-hidden="true"><path d="M4.5 7.5l3-3M5 3l1.5-1.5a2 2 0 013 3L8 6M7 9l-1.5 1.5a2 2 0 01-3-3L4 6" fill="none" stroke="#0255a3" stroke-width="1.3"/></svg>
        www.marrowbyferryline.com
      </li>
    </ul>
    <p class="wordmark"><span class="name">Marrowby</span><span class="tagline">Water Taxi and Transport</span></p>
  </section>

  <section class="card card--back" aria-label="Business card back">
    <div class="sea-photo" role="img" aria-label="Photo of a boat wake trailing across a bay toward mountains at sunset"></div>
    <p class="wordmark"><span class="name">Marrowby</span><span class="tagline">Water Taxi and Transport</span></p>
  </section>
</main>
</body>
</html>
```